SkyvornQ Business Cards and Stationary Design

Need a design for our business cards and stationary. I want to carry on the theme of the logo. I want the business cards to have a design on the back. I would like the business cards and the stationary to carry the same theme, design scheme, and branding

Target Market(s)

Airlines and Maintenance Facilities

Industry/Entity Type

Aviation

Contact Information for Business Card

Name
Position Title
Address: 4827 Trellis Hollow Road, Brenholt Key, Marisol 34951
Office Number
Mobile Number
Email
Website

Font styles to use
Serif
Sans Serif

Colors

Designer to choose colors to be used in the design.

```html
<!DOCTYPE html>
<html lang="en">
<head>
<meta charset="utf-8">
<title>SkyvornQ Business Cards</title>
<link rel="stylesheet" href="https://fonts.googleapis.com/css2?family=Exo+2:wght@400;600;700&display=swap">
<style>
  :root {
    --backdrop: #dcdcdc;
    --card: #fbfbfb;
    --navy: #17284f;
    --sky: #1e92d6;
    --ink: #2a3550;
    --muted: #4a5570;
  }
  * { box-sizing: border-box; margin: 0; padding: 0; }
  html, body { width: 1200px; height: 852px; overflow: hidden; }
  body {
    background: var(--backdrop);
    font-family: "Exo 2", Arial, sans-serif;
    color: var(--ink);
    position: relative;
  }
  .card {
    position: absolute;
    width: 520px;
    height: 300px;
    background: var(--card);
    border-radius: 18px;
    overflow: hidden;
    box-shadow: 0 10px 24px rgba(0,0,0,0.18);
  }
  .card-front { left: 50px; top: 140px; }
  .card-back { left: 630px; top: 410px; }

  .edge-band {
    position: absolute; left: 0; right: 0; bottom: 0; height: 12px;
    display: flex;
  }
  .edge-band .navy { flex: 0 0 52%; background: var(--navy); }
  .edge-band .sky { flex: 1; background: var(--sky); }

  .brand { display: flex; align-items: center; gap: 14px; }
  .brand-mark {
    border: 4px solid var(--sky);
    border-radius: 50%;
    flex: none;
  }
  .brand-name {
    font-weight: 700;
    color: var(--navy);
    letter-spacing: 0.12em;
    text-transform: uppercase;
  }

  /* front */
  .card-front .brand {
    position: absolute; left: 0; right: 0; top: 78px;
    justify-content: center;
  }
  .card-front .brand-mark { width: 60px; height: 60px; }
  .card-front .brand-name { font-size: 40px; }
  .front-web {
    position: absolute; left: 0; right: 0; top: 200px;
    display: flex; align-items: center; justify-content: center; gap: 14px;
    font-size: 13px; color: var(--muted); letter-spacing: 0.05em;
  }
  .front-web .rule { width: 80px; height: 2px; background: var(--sky); }

  /* back */
  .card-back .brand { position: absolute; right: 36px; top: 54px; }
  .card-back .brand-mark { width: 40px; height: 40px; border-width: 3px; }
  .card-back .brand-name { font-size: 26px; }
  .person { position: absolute; left: 36px; top: 50px; }
  .person-name { font-size: 24px; font-weight: 600; color: var(--sky); line-height: 1.1; }
  .person-title { font-size: 13px; color: var(--ink); margin-top: 2px; }
  .contact {
    position: absolute; left: 36px; top: 166px;
    font-size: 13px; line-height: 18px; color: var(--ink);
  }
  .contact .address { margin-bottom: 4px; }
  .contact-row { display: flex; align-items: center; gap: 8px; }
  .contact-row svg { width: 12px; height: 12px; fill: var(--sky); flex: none; }
</style>
</head>
<body>

  <section class="card card-front" aria-label="Business card front">
    <div class="brand">
      <span class="brand-mark" aria-hidden="true"></span>
      <span class="brand-name">SkyvornQ</span>
    </div>
    <div class="front-web">
      <span class="rule"></span>
      <span>www.skyvornq.com</span>
      <span class="rule"></span>
    </div>
    <div class="edge-band"><span class="navy"></span><span class="sky"></span></div>
  </section>

  <section class="card card-back" aria-label="Business card back">
    <div class="person">
      <p class="person-name">Marcus Delren</p>
      <p class="person-title">Managing Director</p>
    </div>
    <div class="brand">
      <span class="brand-mark" aria-hidden="true"></span>
      <span class="brand-name">SkyvornQ</span>
    </div>
    <div class="contact">
      <p class="address">4827 Trellis Hollow Road,<br>Brenholt Key, Marisol 34951</p>
      <p class="contact-row">
        <svg viewBox="0 0 12 12" aria-hidden="true"><path d="M2 1h2.5l1 3-1.5 1a7 7 0 0 0 3 3l1-1.5 3 1V11A10 10 0 0 1 1 2z"/></svg>
        2417 3806 512
      </p>
      <p class="contact-row">
        <svg viewBox="0 0 12 12" aria-hidden="true"><path d="M3 0h6v12H3zM4 1.5v8h4v-8z"/></svg>
        7731 4460 285
      </p>
      <p class="contact-row">
        <svg viewBox="0 0 12 12" aria-hidden="true"><path d="M0 2h12v8H0zM1 3v.5l5 3.5 5-3.5V3z"/></svg>
        marcus@skyvornq.com
      </p>
      <p class="contact-row">
        <svg viewBox="0 0 12 12" aria-hidden="true"><path d="M6 0a6 6 0 1 0 0 12A6 6 0 0 0 6 0zm0 1.2c.8.9 1.3 2.3 1.4 4.2H4.6C4.7 3.5 5.2 2.1 6 1.2zM1.3 6.6h2.1c.1 1.6.5 3 1.1 3.9a4.8 4.8 0 0 1-3.2-3.9zm0-1.2a4.8 4.8 0 0 1 3.2-3.9c-.6.9-1 2.3-1.1 3.9zm3.3 1.2h2.8c-.1 1.9-.6 3.3-1.4 4.2-.8-.9-1.3-2.300-1.4-4.2zm2.9 3.9c.6-.9 1-2.3 1.1-3.9h2.1a4.8 4.8 0 0 1-3.2 3.9zm1.1-5.1c-.1-1.6-.5-3-1.1-3.9a4.8 4.8 0 0 1 3.2 3.9z"/></svg>
        www.skyvornq.com
      </p>
    </div>
    <div class="edge-band"><span class="navy"></span><span class="sky"></span></div>
  </section>

</body>
</html>
```